Product label design needed for an odor removal line of products.

I need a label designed for an odor removal product line. There are eight additional odor removal products that I will need labels designed for so the winner will have additional work from me. I would like each of those products to have a similar look and feel in each one. This contest is for one of the products. The Willow Crest 738 (would love a better name if you are so inclined -many people know what it is by the 738). The no smell formula does not mask odors, it eliminates odors at their source . Also Reduces Allergens! Simply open silver packet and place in dispenser. Great for use in cars, near pet beds or litter boxes, near diaper pails -anywhere odors are a problem. Lasts 60-90 days. Safe to use. Other uses: Nursing homes, hotel rooms, locker rooms, teenage boy rooms, basements... Eco Friendly! No VOC's or phthalates! Do not consume. Keep out of reach of children and pets. Replace every 60-90 days. I put the picture of my logo , the product as it is packaged and a picture of the actual product and the dispenser it will go in. the package is 4x5 in silver packet with .25 seam on the side and .5 seam on the top and bottom. (Dispenser will have a label with reorder information on it. to be designed later) You do not have to put all information provided on the label. It is to be used as you see fit. I tend to like clean, bold designs but am open to all options. Prefer not to use word air freshener.

Target Market(s)

Men and women between 30-65

Industry/Entity Type

Cleaning Product

Font styles to use
Sans Serif

Colors
acd136
9bcb3c
ffffff

Requirements
Must have
• ability for concept/look to be used for a laundry product, smaller odor elimination pouch, odor removing canister and spray as well
Nice to have
• I like greens but am open to designers to decide
Should not have
• word air freshener

```html
<!DOCTYPE html>
<html lang="en">
<head>
<meta charset="utf-8">
<title>The Willow Crest 738 – Packet Label</title>
<link href="https://fonts.googleapis.com/css2?family=Barlow:wght@400;600&display=swap" rel="stylesheet">
<style>
  :root {
    --page-bg: #efefef;
    --packet-dark: #3b3c3e;
    --packet-silver-light: #d9d9da;
    --packet-silver-mid: #8c8d8f;
    --seam: #5a5b5d;
    --brand-green: #8dc63f;
    --brand-green-deep: #6aa531;
    --white: #ffffff;
    --pill-text: #4a4b4d;
  }
  * { box-sizing: border-box; margin: 0; padding: 0; }
  html, body {
    width: 1200px;
    height: 900px;
    overflow: hidden;
    background: var(--page-bg);
    font-family: "Barlow", sans-serif;
  }
  .stage {
    width: 1200px;
    height: 900px;
    display: flex;
    align-items: center;
    justify-content: center;
  }
  .packet {
    position: relative;
    width: 500px;
    height: 700px;
    background: linear-gradient(
      to bottom,
      var(--packet-silver-light) 0%,
      var(--packet-silver-mid) 30%,
      var(--packet-dark) 40%,
      var(--packet-dark) 100%
    );
    display: flex;
    flex-direction: column;
    align-items: center;
    overflow: hidden;
  }
  .seam {
    position: absolute;
    left: 0;
    width: 100%;
    height: 44px;
  }
  .seam--top { top: 0; }
  .seam--bottom { bottom: 0; }
  .brand {
    margin-top: 110px;
    width: 250px;
    height: 250px;
    border-radius: 50%;
    background: var(--white);
    display: flex;
    align-items: center;
    justify-content: center;
  }
  .brand-badge {
    width: 226px;
    height: 226px;
    border-radius: 50%;
    background: var(--brand-green);
    display: flex;
    flex-direction: column;
    align-items: center;
    justify-content: center;
    gap: 14px;
  }
  .brand-dot {
    width: 96px;
    height: 96px;
    border-radius: 50%;
    background: var(--packet-dark);
  }
  .brand-name {
    font-weight: 600;
    font-size: 21px;
    letter-spacing: 2px;
    color: var(--packet-dark);
    text-transform: uppercase;
  }
  .product-title {
    margin-top: 40px;
    text-align: center;
    color: var(--brand-green);
    font-weight: 600;
    text-transform: uppercase;
    line-height: 1.05;
  }
  .product-title .line-one { display: block; font-size: 44px; }
  .product-title .line-two { display: block; font-size: 46px; }
  .claim-pill {
    margin-top: 26px;
    background: var(--white);
    color: var(--pill-text);
    font-size: 16px;
    padding: 5px 28px;
    border-radius: 16px 4px 16px 4px;
  }
  .usage-note {
    margin-top: 22px;
    color: var(--white);
    font-size: 15px;
    text-align: center;
    line-height: 1.35;
  }
</style>
</head>
<body>
  <main class="stage">
    <section class="packet" aria-label="The Willow Crest 738 packet label">
      <svg class="seam seam--top" viewBox="0 0 500 44" preserveAspectRatio="none" aria-hidden="true">
        <rect width="500" height="44" fill="#b9babb"/>
        <g stroke="#7d7e80" stroke-width="1.5">
          <line x1="0" y1="8" x2="500" y2="8"/>
          <line x1="0" y1="16" x2="500" y2="16"/>
          <line x1="0" y1="24" x2="500" y2="24"/>
          <line x1="0" y1="32" x2="500" y2="32"/>
          <line x1="0" y1="40" x2="500" y2="40"/>
        </g>
      </svg>

      <div class="brand">
        <div class="brand-badge">
          <span class="brand-dot"></span>
          <span class="brand-name">Brightmoor Living</span>
        </div>
      </div>

      <h1 class="product-title">
        <span class="line-one">The Willow</span>
        <span class="line-two">Crest 738</span>
      </h1>

      <p class="claim-pill">Eco Friendly! &nbsp;|&nbsp; No VOC's or phthalates!</p>

      <p class="usage-note">Keep out of reach of children and pets.<br>Replace every 60-90 days</p>

      <svg class="seam seam--bottom" viewBox="0 0 500 44" preserveAspectRatio="none" aria-hidden="true">
        <rect width="500" height="44" fill="#2f3032"/>
        <g stroke="#4c4d4f" stroke-width="1.5">
          <line x1="0" y1="4" x2="500" y2="4"/>
          <line x1="0" y1="12" x2="500" y2="12"/>
          <line x1="0" y1="20" x2="500" y2="20"/>
          <line x1="0" y1="28" x2="500" y2="28"/>
          <line x1="0" y1="36" x2="500" y2="36"/>
        </g>
      </svg>
    </section>
  </main>
</body>
</html>
```